Retail Jewelry Business Card Design Project

We are in need of a new business card design for a retail jewelry store. This store is in the business of fine jewelry including but not specific to bridal jewelry, diamonds, designer jewelry and watches.

This store has been in business for 20 years but continues to strive for a modern professional appeal. The main colors use for this business are a royal blue, white and silver.

Target Market(s)

Target market is ages 18-50

Industry/Entity Type

Jewelry

Requirements
Must have
• Sales Person Name
Sales Person Email Address

Store Address
Store Phone
Website

Standard business card size. No odd shapes or sizes.
Nice to have
• Overall modern feel for card.

We have thought that a design with a nice feature of the logo on the back of the card would be nice but open to ideas.
Should not have
• No specific images of jewelry should be used.

```html
<!DOCTYPE html>
<html lang="en">
<head>
<meta charset="utf-8">
<title>Laurent Hale Fine Jewelry – Business Cards</title>
<link rel="stylesheet" href="https://fonts.googleapis.com/css2?family=Jost:wght@400;500;600&display=swap">
<style>
  :root {
    --royal-blue: #2e3690;
    --wave-lilac: #7a7fc4;
    --card-white: #ffffff;
    --silver: #c9ccd3;
    --stage: #eceef2;
    --ink-soft: #2a2f6e;
  }
  * { box-sizing: border-box; margin: 0; padding: 0; }
  html, body { width: 1200px; height: 751px; overflow: hidden; }
  body {
    background: var(--stage);
    font-family: "Jost", sans-serif;
    position: relative;
  }
  .card {
    position: absolute;
    top: 227px;
    width: 525px;
    height: 300px;
    border-radius: 24px;
    overflow: hidden;
    box-shadow: 0 6px 18px rgba(30, 34, 80, 0.18);
  }
  .card--front { left: 48px; background: var(--card-white); }
  .card--back  { left: 627px; background: var(--royal-blue); color: var(--card-white); }

  /* front */
  .front-wave { position: absolute; left: 0; bottom: 0; width: 525px; height: 150px; }
  .brand-name {
    position: absolute;
    left: 40px; top: 72px;
    width: 220px;
    font-weight: 500;
    color: var(--royal-blue);
    text-align: center;
    line-height: 1.15;
  }
  .brand-name .brand-main { display: block; font-size: 31px; }
  .brand-name .brand-sub { display: block; font-size: 15px; letter-spacing: 3px; text-transform: uppercase; margin-top: 4px; }
  .divider {
    position: absolute;
    left: 282px; top: 36px;
    width: 2px; height: 110px;
    background: linear-gradient(var(--silver), rgba(201,204,211,0));
  }
  .contact { position: absolute; left: 298px; top: 30px; color: var(--ink-soft); }
  .contact-name { font-size: 19px; font-weight: 600; color: var(--royal-blue); margin-bottom: 12px; }
  .contact-list { list-style: none; font-size: 13.5px; }
  .contact-list li { display: flex; align-items: center; gap: 7px; margin-bottom: 6px; }
  .contact-list svg { width: 11px; height: 11px; flex: none; fill: var(--royal-blue); }
  .store-address {
    position: absolute;
    left: 34px; bottom: 24px;
    color: var(--card-white);
    font-size: 14px;
    font-style: normal;
    line-height: 1.45;
    letter-spacing: 0.5px;
  }

  /* back */
  .back-brand {
    position: absolute;
    left: 0; right: 0; top: 86px;
    text-align: center;
    font-weight: 500;
    line-height: 1.15;
  }
  .back-brand .brand-main { display: block; font-size: 46px; }
  .back-brand .brand-sub { display: block; font-size: 20px; letter-spacing: 4px; text-transform: uppercase; margin-top: 6px; }
  .back-web {
    position: absolute;
    left: 0; right: 0; top: 226px;
    text-align: center;
    font-size: 14px;
    letter-spacing: 3px;
  }
</style>
</head>
<body>

<section class="card card--front" aria-label="Business card front">
  <svg class="front-wave" viewBox="0 0 525 150" preserveAspectRatio="none" aria-hidden="true">
    <path d="M0 48 C150 18 330 28 525 0 L525 9 C330 38 150 30 0 55 Z" fill="var(--wave-lilac)"/>
    <path d="M0 60 C160 32 330 42 525 16 L525 150 L0 150 Z" fill="var(--royal-blue)"/>
  </svg>

  <div class="brand-name">
    <span class="brand-main">Laurent Hale</span>
    <span class="brand-sub">Fine Jewelry</span>
  </div>

  <div class="divider"></div>

  <div class="contact">
    <p class="contact-name">Laurent Hale Whitmore</p>
    <ul class="contact-list">
      <li>
        <svg viewBox="0 0 12 12"><path d="M3 1 L5 3.5 L4 5 Q5 7 7 8 L8.5 7 L11 9 L10 11 Q5 11 2.5 8 Q0.5 5 1 2 Z"/></svg>
        555-204-7731
      </li>
      <li>
        <svg viewBox="0 0 12 12"><path d="M1 3 H11 V10 H1 Z M1 3 L6 7 L11 3" stroke="#fff" stroke-width="0.8"/></svg>
        laurent@laurenthalejewelry.com
      </li>
      <li>
        <svg viewBox="0 0 12 12"><circle cx="6" cy="6" r="5"/><path d="M1 6 H11 M6 1 V11" stroke="#fff" stroke-width="0.8"/></svg>
        www.laurenthalejewelry.com
      </li>
    </ul>
  </div>

  <address class="store-address">
    2280 Meridian Avenue<br>
    Harbor City, FL 32011
  </address>
</section>

<section class="card card--back" aria-label="Business card back">
  <div class="back-brand">
    <span class="brand-main">Laurent Hale</span>
    <span class="brand-sub">Fine Jewelry</span>
  </div>
  <p class="back-web">www.laurenthalejewelry.com</p>
</section>

</body>
</html>
```